Flyer for the Radiant Harvest Worship Day

I am looking to create a flyer for a one day prayer retreat our church is organizing.
This flyer will be posted on social media, websites and will also be printed so it can be mailed to people.
I am looking for something professional, with good use of our logo and band colors (logo colors).
I am counting on the designer's skill, creativity, art and knowledge of media communication to produce a flyer that will effectively and quickly convey the message we are trying to spread.
CONTENT OF THE FLYER:
Event title: Radiant Harvest Worship Day
Date: Tuesday July 2nd, 2019
Time: 11:00AM - 7:00PM
Belmora Hotel, 4875 Wexley Avenue, Ashbury Falls, Westmark 00417 (Room: Juniper)
Event Key words to highlight what the event is about: Prayer, Sharing the Word, Panel discussion, prophecy, Impartation.
Key phrases:
A one day prayer retreat.
Jesus Chris is Lord
Contact info:
www.tolvex.org
Phone: 207 555 3184
Email: contact@brookhavenfold.org

```html
<!DOCTYPE html>
<html lang="en">
<head>
<meta charset="utf-8">
<title>Radiant Harvest Worship Day</title>
<link href="https://fonts.googleapis.com/css2?family=Open+Sans:wght@300;400;700;800&family=Raleway:wght@300;400;500&display=swap" rel="stylesheet">
<style>
  :root {
    --orange: #f7941d;
    --frame-orange: #d4861f;
    --navy: #1b3a64;
    --logo-navy: #0d3a66;
    --white: #ffffff;
    --night: #0a1120;
  }
  * { margin: 0; padding: 0; box-sizing: border-box; }
  html, body { width: 1200px; height: 800px; overflow: hidden; background: var(--night); }
  .flyer {
    position: relative; width: 1200px; height: 800px; overflow: hidden;
    font-family: "Open Sans", sans-serif; color: var(--white);
  }
  .backdrop {
    position: absolute; inset: 0;
    background:
      linear-gradient(to bottom, transparent 0 82%, rgba(5,5,8,0.95) 88%, #050507 100%),
      radial-gradient(ellipse 300px 280px at 830px 540px, #fffbe0 0%, #fbe7a6 25%, #eab56a 50%, rgba(160,110,80,0.55) 75%, rgba(40,50,70,0) 100%),
      linear-gradient(160deg, #070d1c 0%, #10203a 35%, #3a4554 60%, #8a7566 80%, #c99a6a 100%);
  }
  .frame { position: absolute; left: 0; top: 0; }
  .logo { position: absolute; left: 66px; top: 118px; display: flex; align-items: center; gap: 14px; }
  .logo-dot { width: 26px; height: 26px; border-radius: 50%; background: var(--orange); }
  .logo-name {
    font-family: "Raleway", sans-serif; font-weight: 500; font-size: 78px;
    letter-spacing: 2px; color: var(--logo-navy); line-height: 1;
  }
  .tagline {
    position: absolute; left: 88px; top: 210px;
    font-family: "Raleway", sans-serif; font-size: 20px; letter-spacing: 1px;
    color: var(--orange);
  }
  .intro { position: absolute; left: 82px; top: 314px; font-family: "Raleway", sans-serif; font-size: 19px; font-weight: 500; line-height: 24px; }
  .intro .accent { color: var(--orange); }
  .contact-heading { position: absolute; left: 75px; top: 459px; font-family: "Raleway", sans-serif; font-size: 19px; font-weight: 500; }
  .contact-label {
    position: absolute; left: 75px; width: 214px; height: 45px;
    background: var(--orange); display: flex; align-items: center; justify-content: center;
    font-family: "Raleway", sans-serif; font-weight: 400; font-size: 19px;
  }
  .contact-value { position: absolute; font-size: 13.5px; line-height: 15.5px; letter-spacing: 0.2px; }
  .title { position: absolute; right: 148px; text-align: right; line-height: 1; }
  .title-main { top: 148px; font-weight: 800; font-size: 100px; letter-spacing: 1px; }
  .title-sub { top: 258px; font-weight: 300; font-size: 56px; }
  .title-year { top: 326px; font-weight: 800; font-size: 86px; color: var(--navy); }
  .when { position: absolute; right: 144px; text-align: right; color: var(--navy); line-height: 1; }
  .when-day { top: 494px; font-weight: 800; font-size: 42px; }
  .when-month { top: 538px; right: 147px; font-weight: 300; font-size: 32px; }
  .when-time { top: 594px; right: 147px; font-weight: 700; font-size: 24px; }
  .when-label { top: 630px; right: 147px; font-size: 11px; }
  .site { position: absolute; left: 600px; top: 714px; font-size: 14px; font-weight: 300; }
  .more { position: absolute; left: 935px; top: 712px; display: flex; align-items: center; gap: 8px; font-size: 14px; }
  .more-square { width: 24px; height: 24px; border-radius: 5px; background: var(--orange); }
</style>
</head>
<body>
<main class="flyer">
  <div class="backdrop" role="img" aria-label="Hilltop silhouette with a cross against a glowing sunset sky"></div>

  <svg class="frame" width="1200" height="800" viewBox="0 0 1200 800" aria-hidden="true">
    <path d="M592 144 V104 H1123 V698 H592 V356" fill="none" stroke="var(--frame-orange)" stroke-width="8" transform="translate(-12 -3)"/>
  </svg>

  <div class="logo"><span class="logo-dot"></span><span class="logo-name">TOLVEX</span></div>
  <p class="tagline">A LIGHT FOR EVERY SHORE</p>

  <p class="intro">A ONE DAY PRAYER RETREAT.<br><span class="accent">JESUS CHRIS IS LORD</span></p>

  <p class="contact-heading">CONTACT INFO:</p>
  <div class="contact-label" style="top:510px">LOCATION:</div>
  <p class="contact-value" style="left:310px;top:509px">BELMORA HOTEL,<br>4875 WEXLEY AVENUE,<br>ASHBURY FALLS, WESTMARK 00417<br>(ROOM: JUNIPER)</p>
  <div class="contact-label" style="top:583px">PHONE:</div>
  <p class="contact-value" style="left:317px;top:599px">207 555 3184</p>
  <div class="contact-label" style="top:656px">EMAIL:</div>
  <p class="contact-value" style="left:315px;top:673px">CONTACT@BROOKHAVENFOLD.ORG</p>

  <h1>
    <span class="title title-main">RADIANT</span>
    <span class="title title-sub">HARVEST WORSHIP DAY</span>
    <span class="title title-year">2019</span>
  </h1>

  <p class="when when-day">Tuesday 2</p>
  <p class="when when-month">JULY</p>
  <p class="when when-time">11:00AM - 7:00PM</p>
  <p class="when when-label">TIME</p>

  <p class="site">www.tolvex.org</p>
  <div class="more">MORE INFO:
    <span class="more-square"></span><span class="more-square"></span><span class="more-square"></span>
  </div>
</main>
</body>
</html>
```